Kelumo.cn needs pages to be re-designed

www.kelumo.cn is our current new site which was launched in April.
We're a financial services website in the crowdfunding space in China to connect borrower's and lender's.

test.kelumo.cn is our test site
u: test
p: newtest
http://test.kelumo.cn/
http://test.kelumo.cn/user/accounts/new_lender
http://test.kelumo.cn/user/accounts/new_borrower
http://test.kelumo.cn/introductions/protection
http://test.kelumo.cn/introductions
http://test.kelumo.cn/introductions/kelumo_admin
http://test.kelumo.cn/introductions/contact
Some of the pages have pop-ups in the bloc's of the pages. Please click the links, to see more content.

User's currently criticize the website for being:
- Too Western looking
- Too simple, too little content
- Content NOT in the pop-ups are too simple
- Pictures are too big and too much blank space
- Relevant information is not there when needed
- The pictures are too generic

What we would like to do is re-design those pages with the same color scheme and style to be more compelling, efficient, non-intimidating and easy-to-use. Our audience is Ages 25-35 predominantly male investors.
We are looking for more ideas to make the content match the style, while bridging western and chinese design. Our ultimate goal is to increase registrants to the website and highlight our core competitive advantages.

Some competitors websites are:
www.fobuxiqi.com
www.tamev.com
www.zzzlendo.com

Reason: Not enough good designs that follow the prompt. Same style, better information layout!

Reason: Still have not received a design we're satisfied with

Reason: WE DONT WANT A COMPLETE REDESIGN OF PAGES . KEEP THE EXACT SAME COLOR AND STYLE - WE WANT CONTENT RE-DESIGN! THE BLOCS ARE TOO SIMPLE - WE WANT MORE CONTENT INSIDE.

Reason: no new designs

Reason: no new designs

Reason: other non-registered pages need to be re-designed

```html
<!DOCTYPE html>
<html lang="zh-CN">
<head>
<meta charset="utf-8">
<title>常见问题 · Kelumo.cn</title>
<link rel="stylesheet" href="https://fonts.googleapis.com/css2?family=Noto+Sans+SC:wght@400;500&display=swap">
<style>
:root{
  --green:#4db82d;
  --green-dark:#3a9a20;
  --ink:#333333;
  --muted:#8a8a8a;
  --line:#e3e3e3;
  --side:#f5f5f5;
  --footer:#c9c9c9;
  --white:#ffffff;
}
*{margin:0;padding:0;box-sizing:border-box}
html,body{width:929px;height:1200px;overflow:hidden;background:var(--white)}
body{font-family:"Noto Sans SC",sans-serif;color:var(--ink);position:relative}
.site-header{position:absolute;left:0;top:0;width:929px;height:71px;background:var(--white)}
.brand{position:absolute;left:66px;top:22px;display:flex;align-items:center;gap:8px}
.brand-dot{width:26px;height:26px;border-radius:50%;background:var(--green)}
.brand-name{font-size:18px;font-weight:500;color:var(--green)}
.main-nav{position:absolute;top:30px;left:496px;display:flex;font-size:11px;color:var(--ink)}
.main-nav a{display:flex;align-items:center;gap:4px;color:inherit;text-decoration:none;margin-right:33px}
.main-nav svg{width:13px;height:13px}
.hero{position:absolute;left:0;top:71px;width:929px;height:271px;
  background:linear-gradient(90deg,#9a9a9a 0%,#cfd0d0 14%,#e9eaea 40%,#f0f1f1 60%,#dcdcdc 80%,#9d9d9d 100%)}
.page-title{position:absolute;left:66px;top:380px;font-size:19px;font-weight:400;color:var(--green)}
.sidebar{position:absolute;left:0;top:342px;width:258px;height:802px;background:var(--side)}
.side-nav{position:absolute;left:0;top:428px;width:261px;list-style:none}
.side-nav li{height:34px;line-height:34px;padding-left:68px;font-size:13px;border-bottom:1px solid #e8e8e8;width:258px}
.side-nav li.active{background:var(--green);color:var(--white);border-bottom:3px solid var(--green-dark);width:261px;position:relative}
.side-nav li.active::after{content:"";position:absolute;right:22px;top:13px;border-left:4px solid var(--white);border-top:4px solid transparent;border-bottom:4px solid transparent}
.faq{position:absolute;left:295px;top:421px;width:582px}
.faq h2{font-size:16px;font-weight:500}
.faq .lead{font-size:10px;color:var(--muted);margin-top:2px;padding-bottom:6px;border-bottom:1px solid var(--line)}
.faq-open{display:flex;justify-content:space-between;margin-top:14px;font-size:12px}
.toggle{color:var(--green);text-decoration:underline}
.answer{margin-top:22px;font-size:11.5px;line-height:20.4px;color:var(--muted)}
.faq-list{list-style:none;margin-top:38px;font-size:12px}
.faq-list li{height:30.8px}
.site-footer{position:absolute;left:0;top:1144px;width:929px;height:56px;background:var(--footer)}
.help{position:absolute;left:70px;top:18px;display:flex;align-items:center;gap:10px;color:var(--white);font-size:12px}
.footer-toggle{position:absolute;left:234px;top:22px;font-size:11px;color:var(--ink)}
.social{position:absolute;right:50px;top:16px;display:flex;gap:14px}
.social span{width:22px;height:22px;border-radius:50%;background:#9a9a9a}
</style>
</head>
<body>
<header class="site-header">
  <div class="brand"><span class="brand-dot"></span><span class="brand-name">Kelumo.cn</span></div>
  <nav class="main-nav">
    <a href="#"><svg viewBox="0 0 14 14"><circle cx="7" cy="7" r="6" fill="none" stroke="#333" stroke-width="1.6"/></svg>首页</a>
    <a href="#"><svg viewBox="0 0 14 14"><path d="M7 1 12 3v4c0 3-2.5 5-5 6-2.5-1-5-3-5-6V3z" fill="none" stroke="#333" stroke-width="1.5"/><path d="M4.5 7 6.5 9 9.5 5" fill="none" stroke="#333" stroke-width="1.4"/></svg>安全</a>
    <a href="#"><svg viewBox="0 0 14 14"><path d="M2 4h10M2 7h10M2 10h10" stroke="#333" stroke-width="1.6"/></svg>投资</a>
    <a href="#"><svg viewBox="0 0 14 14"><rect x="3" y="1.5" width="8" height="11" fill="none" stroke="#333" stroke-width="1.5"/><path d="M5 6h4M5 9h4" stroke="#333" stroke-width="1.2"/></svg>贷款</a>
    <a href="#"><svg viewBox="0 0 14 14"><rect x="3" y="6" width="8" height="7" fill="#333"/><path d="M4.5 6V4a2.5 2.5 0 0 1 5 0v2" fill="none" stroke="#333" stroke-width="1.5"/></svg>登录 ▾</a>
  </nav>
</header>

<div class="hero" role="img" aria-label="白板上写满图表与草图，中央是绿色大字 FAQ，右侧一位身穿西装的男士背对画面思考"></div>

<aside class="sidebar"></aside>
<h1 class="page-title">常见问题</h1>
<ul class="side-nav">
  <li class="active">投资</li>
  <li>贷款</li>
  <li>其他</li>
</ul>

<main class="faq">
  <h2>投資常見問題</h2>
  <p class="lead">單擊某個主題，查看有關該主題的幫助文章。</p>
  <div class="faq-open"><span>1. 注册过程中如有中断，再次进入平台是否可以继续注册过程?</span><span class="toggle">点击收缩</span></div>
  <div class="answer">
    <p>为减少投资风险，可路摩规定投资人在投资借款项目时，每个借款项目只能投资一次，并且只能投资该借款项目额度的80%。</p>
    <p>出借资金以后，如果每月账户的还款不足100元，将无法进行再投资，会影响到最终的年化收益，每月满足100元进行再投资才可以不断滚动生息达到年化12%-15%的收益。</p>
    <p>投资人发起债权转让只能转让单笔大于100元的债权，低于100元的债权由于系统限制将无法通过。</p>
    <p>如果投资人选择了自动投标，请尽量把投资期限设置成12个月或18个月，这样便于系统平台尽快将您的资金投资出去。</p>
    <p>为避免个别信用卡套现投机行为的出现，可路摩规定投资人累计充值1000元以上，且不投资就直接提现的行为会被禁止通过，鉴于部分新客户是为了测试平台真实性及提现效率，我们建议测试金额在1000元（含）以内，100元——1000元（含）以内的上述行为仍然予以支持。</p>
  </div>
  <ul class="faq-list">
    <li>2. 出借人（或借款人）可不可以再同时注册借款人（或出借人）账户?</li>
    <li>3. 可路摩与其他同类公司的区别是什么?</li>
    <li>4. 如何提供信用等级和信用额度?</li>
    <li>5. 信用等级的高低对用户借款有什么影响?</li>
    <li>6. 加分资料都包括哪些资料?</li>
    <li>7. 注册过程中如有中断，再次进入平台是否可以继续注册过程?</li>
    <li>8. 出借人（或借款人）可不可以再同时注册借款人（或出借人）账户?</li>
    <li>9. 可路摩与其他同类公司的区别是什么?</li>
    <li>10. 如何提供信用等级和信用额度?</li>
    <li>11. 信用等级的高低对用户借款有什么影响?</li>
    <li>12. 加分资料都包括哪些资料?</li>
  </ul>
</main>

<footer class="site-footer">
  <div class="help"><svg width="22" height="20" viewBox="0 0 22 20"><rect x="8" y="1" width="13" height="9" rx="2" fill="#fff"/><circle cx="5" cy="12" r="3" fill="#fff"/><path d="M0 20a5 5 0 0 1 10 0z" fill="#fff"/></svg>我需要帮助</div>
  <div class="footer-toggle">显示页脚信息+</div>
  <div class="social"><span></span><span></span><span></span><span></span></div>
</footer>
</body>
</html>
```